Cat-products company needs smart, yet endearing, business card

We need a business card design for a new, but up-and-running, business based in Honolulu, Hawaii. The business is Purrnest Nook Co. Our first product is the most environmentally-friendly cat grass kit ever seen on the planet. Future products, currently in the R&D phase, will include a variety of exciting cat scratchers. We also do consulting work to help apartment-dwellers make their home more cat-friendly and, in the future, plan on doing full, custom installs of structure to create high walkways for cats.

Target Market(s)

Middle-aged, apartment-dwelling, middle-class workers who own 1 or more cats and who dote on them.

Industry/Entity Type

Pet Care

Contact Information for Business Card

A striking, professional, yet warm and friendly design is what we're after.

Font styles to use
Serif
Sans Serif
Other font styles liked:
• Comfortaa

Colors

Designer to choose colors to be used in the design.

Requirements
Must have
• The company logo: (see attachment)
• The company name: Purrnest Nook Co
• The web address: www.purrnestnookco.com
• Email: support@purrnestnookco.com
• Phone: +1 (808) 571 6023
• Update (Fri Jun 30 3017 7:45pm Hawaii Time) I would like, is possible, uploaded picture of the cat grass kit on the back of the card with some text along the lines of: Purrnest Nook Co - Maker Of The Leafiest Feline Sprout Set Yet
Nice to have
• A cat picture, cartoon, real or silhouette that illustrates cats in action and/or relaxing; ie using the apartment space to live, play and relax in and being well-contented.
• Most of the website is done in the font: Comfortaa. It might be nice to continue using this for brand consistency.
Should not have
• Hard-to-read fonts.

```html
<!DOCTYPE html>
<html lang="en">
<head>
<meta charset="utf-8">
<title>Purrnest Nook Co — Business Card</title>
<link rel="stylesheet" href="https://fonts.googleapis.com/css2?family=Comfortaa:wght@700&family=Open+Sans:wght@400;700&display=swap">
<style>
  :root {
    --amber: #fdb300;
    --cocoa: #54332b;
    --card-light: #e9e7e6;
    --ink: #2e2a28;
    --backdrop: #f3f0ec;
  }
  * { box-sizing: border-box; margin: 0; padding: 0; }
  html, body {
    width: 1200px; height: 900px; overflow: hidden;
    background: var(--backdrop);
  }
  .canvas {
    width: 1200px; height: 900px;
    display: flex; flex-direction: column; align-items: center; justify-content: center;
    gap: 40px;
  }
  .card {
    width: 700px; height: 400px;
    border-radius: 4px;
    box-shadow: 0 6px 18px rgba(60, 40, 20, 0.18);
    position: relative;
    overflow: hidden;
  }
  /* Front */
  .card--front {
    background: var(--amber);
    display: flex; align-items: center; justify-content: center; gap: 22px;
  }
  .brand-mark {
    width: 64px; height: 64px; background: var(--cocoa);
  }
  .brand-name--front {
    font-family: "Comfortaa", sans-serif; font-weight: 700;
    font-size: 50px; color: #ffffff; letter-spacing: -0.5px;
  }
  /* Back */
  .card--back { background: var(--card-light); }
  .brand-name--back {
    position: absolute; left: 48px; top: 62px;
    font-family: "Comfortaa", sans-serif; font-weight: 700;
    font-size: 46px; line-height: 1.08; color: var(--amber);
  }
  .brand-block {
    position: absolute; right: 56px; top: 60px;
    width: 210px; height: 210px; background: var(--cocoa);
  }
  .person {
    position: absolute; left: 48px; top: 222px;
    font-family: "Open Sans", sans-serif;
  }
  .person__name {
    font-weight: 700; font-size: 19px; color: var(--amber);
    letter-spacing: 0.5px; text-transform: uppercase;
  }
  .person__role { font-size: 15px; color: var(--ink); margin-top: 1px; }
  .contact {
    position: absolute; left: 48px; top: 292px;
    list-style: none;
    font-family: "Open Sans", sans-serif; font-size: 16px; color: var(--ink);
  }
  .contact__item { display: flex; align-items: center; gap: 10px; height: 26px; }
  .contact__icon { width: 14px; height: 14px; flex: none; }
</style>
</head>
<body>
<main class="canvas">
  <section class="card card--front" aria-label="Card front">
    <div class="brand-mark"></div>
    <h1 class="brand-name--front">Purrnest Nook Co</h1>
  </section>

  <section class="card card--back" aria-label="Card back">
    <h2 class="brand-name--back">Purrnest<br>Nook Co</h2>
    <div class="brand-block"></div>

    <div class="person">
      <p class="person__name">Maren Kealoha</p>
      <p class="person__role">Managing Director</p>
    </div>

    <ul class="contact">
      <li class="contact__item">
        <svg class="contact__icon" viewBox="0 0 16 16" aria-hidden="true">
          <path fill="#fdb300" d="M3.6 1.2l2.3 2.4-1.3 1.9c.9 2 2.6 3.8 4.8 4.9l1.9-1.3 2.4 2.3-1.6 2.5C7 13.6 2.4 9 1.1 2.8z"/>
        </svg>
        <span>+1 (808) 571 6023</span>
      </li>
      <li class="contact__item">
        <svg class="contact__icon" viewBox="0 0 16 16" aria-hidden="true">
          <rect x="1" y="3" width="14" height="10" fill="#fdb300"/>
          <path d="M1.5 3.5L8 9l6.5-5.5" fill="none" stroke="#e9e7e6" stroke-width="1.3"/>
        </svg>
        <span>support@purrnestnookco.com</span>
      </li>
      <li class="contact__item">
        <svg class="contact__icon" viewBox="0 0 16 16" aria-hidden="true">
          <circle cx="8" cy="8" r="7" fill="#fdb300"/>
          <path d="M1 8h14M8 1c-3 3.5-3 10.5 0 14M8 1c3 3.5 3 10.5 0 14" fill="none" stroke="#e9e7e6" stroke-width="1"/>
        </svg>
        <span>www.purrnestnookco.com</span>
      </li>
    </ul>
  </section>
</main>
</body>
</html>
```